Moxy Fen needs some awesome stationary

Do you have what it takes to get my brand? You either do or you don't, have a crack at a design and you my just win my business.

I don't want to waste your or my time, so put your creative genius on either a business card or envelope.

I however need a package of stationary that follows the same brand. I will message you to complete the remaining should I like your first submission.

Here is what I need, have a go!

Basically I need the following for my small business based in melbourne.
- Letterhead (printer ready and MS Word)
- Business Card
- Compliments Slip
- Envelope
- Proposal Cover Page (MS Word only)
- Presentation Folder
- Marbled Fox Cards
- Student Name Tent
- Index Cards
- Vell-Ka

I am establishing the brand and it must be modern, professional but also relaxed; that is not formal and not corporate. It represents a company are leaders, but small enough to care and operate like a bunch of friends. We are bringing people and conversations back to business, and turfing out all the bureaucracy and crazy and wasteful procedures. Its about "lets talk and figure it out together and find even better ways".

Target Market(s)

Mainly companies that build software products, but Agile practices are used in many other industries (even graphic design projects)

Industry/Entity Type

Information Technology

Font styles to use
Sans Serif

Colors
3176b5
aaaaaa

Requirements
Must have
• I like curves and circles and not boxes or rectangles.
• I want a colour rich design with my brand colours, but it must be balanced.
• I want more modern than traditional, but simple modern
Should not have
• Not corporate
• Please don't waste my time if your not going to think about it.
• Don't mess with my primary logo
• Don't change my colours
• Don't overlay logo on image

```html
<!DOCTYPE html>
<html lang="en">
<head>
<meta charset="utf-8">
<title>Moxy Fen — Stationery Set</title>
<link href="https://fonts.googleapis.com/css2?family=Open+Sans:wght@400;600;700&family=Pinyon+Script&display=swap" rel="stylesheet">
<style>
  :root {
    --brand-blue: #3d65a3;
    --brand-grey: #a9aaac;
    --spine-grey: #8e9aab;
    --paper: #f4f4f4;
    --backdrop: #e8e9ea;
    --ink: #4a4f57;
  }
  * { margin: 0; padding: 0; box-sizing: border-box; }
  html, body { width: 1200px; height: 822px; overflow: hidden; }
  body {
    background: var(--backdrop);
    font-family: "Open Sans", Arial, sans-serif;
    color: var(--ink);
    position: relative;
  }
  .sheet { position: absolute; background: var(--paper); overflow: hidden; }
  .wordmark { font-weight: 600; color: var(--brand-blue); white-space: nowrap; line-height: 1; display: flex; align-items: center; gap: 4px; }
  .wordmark-dot { display: inline-block; border-radius: 50%; background: var(--brand-grey); }
  .tiny { font-size: 4.6px; line-height: 1.5; color: var(--ink); white-space: nowrap; }

  /* Letterhead */
  .letterhead { left: 349px; top: 111px; width: 313px; height: 446px; }
  .letterhead .wordmark { position: absolute; left: 30px; top: 48px; font-size: 11px; }
  .letterhead .wordmark-dot { width: 9px; height: 9px; }
  .letterhead-address { position: absolute; right: 115px; top: 40px; text-align: right; }
  .letterhead-contact { position: absolute; left: 220px; top: 34px; }
  .contact-row { display: flex; align-items: center; gap: 4px; }
  .contact-icon { width: 4px; height: 4px; fill: var(--brand-blue); flex: none; }

  /* Presentation folder */
  .folder { left: 704px; top: 91px; width: 371px; height: 468px; background: var(--brand-blue); }
  .folder-spine { position: absolute; left: 0; top: 0; width: 22px; height: 100%; background: var(--spine-grey); }
  .folder .wordmark { position: absolute; left: 22px; right: 0; top: 362px; justify-content: center; color: #f1f1f1; font-size: 32px; }

  /* Business card front */
  .card-front { left: 168px; top: 373px; width: 142px; height: 80px; background: var(--brand-blue); }
  .card-front svg { position: absolute; inset: 0; }
  .card-front-details { position: absolute; left: 8px; top: 13px; color: #fff; }
  .card-front-details .tiny { color: #e6ebf3; font-size: 3.6px; }
  .card-name { font-size: 5px; font-weight: 700; letter-spacing: .1px; }
  .card-front .wordmark { position: absolute; left: 86px; top: 52px; font-size: 8px; }

  /* Business card back */
  .card-back { left: 168px; top: 476px; width: 142px; height: 80px; }
  .card-back svg { position: absolute; inset: 0; }
  .card-back-text {
    position: absolute; right: 5px; top: 0; height: 80px;
    writing-mode: vertical-rl; transform: rotate(180deg);
    text-align: center; color: #fff; line-height: 1.1;
  }
  .card-back-text .wordmark { display: block; color: #fff; font-size: 11.5px; line-height: 1.1; }
  .card-back-phone { font-size: 6px; letter-spacing: .6px; white-space: nowrap; }

  /* DL envelope front */
  .envelope-front { left: 47px; top: 602px; width: 352px; height: 168px; }
  .envelope-front .wordmark { position: absolute; left: 20px; top: 50px; font-size: 9.5px; }
  .envelope-front .wordmark-dot { width: 8px; height: 8px; }
  .envelope-front .tiny { position: absolute; left: 20px; top: 63px; font-size: 4.2px; }

  /* Envelope back */
  .envelope-back { left: 433px; top: 602px; width: 351px; height: 166px; }
  .envelope-back svg { position: absolute; left: 0; top: 0; }
  .envelope-flap-mark { position: absolute; left: 0; right: 0; top: 22px; display: flex; flex-direction: column; align-items: center; gap: 3px; }
  .envelope-flap-mark .wordmark { color: #fff; font-size: 8px; }
  .envelope-flap-mark .tiny { color: #dfe6f1; font-size: 3.8px; }

  /* Compliments slip */
  .compliments { left: 815px; top: 602px; width: 351px; height: 168px; }
  .compliments .wordmark { position: absolute; left: 17px; top: 48px; font-size: 9.5px; }
  .compliments .wordmark-dot { width: 8px; height: 8px; }
  .compliments-script { position: absolute; right: 22px; top: 116px; font-family: "Pinyon Script", cursive; color: var(--brand-blue); font-size: 20px; line-height: 1; }
  .compliments-footer { position: absolute; left: 17px; right: 17px; top: 130px; }
  .compliments-footer .tiny { font-size: 4px; line-height: 1.45; }
  .compliments-rule { height: 0; border-top: .5px solid #b8bcc3; margin: 1px 0 1px; }
  .compliments-web { color: var(--brand-blue); font-weight: 600; letter-spacing: .3px; }
</style>
</head>
<body>

  <section class="sheet letterhead" aria-label="Letterhead">
    <div class="wordmark"><span class="wordmark-dot"></span>Moxy Fen</div>
    <div class="letterhead-address tiny">
      PO Box 4417<br>Kelbrook Lower<br>VIC 3190, Australia
    </div>
    <div class="letterhead-contact tiny">
      <div class="contact-row"><svg class="contact-icon" viewBox="0 0 10 10"><path d="M2 0h2l1 3-1.5 1a6 6 0 0 0 2.5 2.5L7 5l3 1v2a2 2 0 0 1-2 2A8 8 0 0 1 0 2a2 2 0 0 1 2-2z"/></svg>1300MOXYFEN</div>
      <div class="contact-row"><svg class="contact-icon" viewBox="0 0 10 10"><rect x="2" y="0" width="6" height="10" rx="1"/></svg>+61 400 555 217</div>
      <div class="contact-row"><svg class="contact-icon" viewBox="0 0 10 10"><rect x="0" y="2" width="10" height="6"/></svg>dale@moxyfen.com.au</div>
      <div class="contact-row"><svg class="contact-icon" viewBox="0 0 10 10"><circle cx="5" cy="5" r="5"/></svg>www.moxyfen.com.au</div>
    </div>
  </section>

  <section class="sheet folder" aria-label="Presentation folder">
    <div class="folder-spine"></div>
    <div class="wordmark">Moxy Fen</div>
  </section>

  <section class="sheet card-front" aria-label="Business card front">
    <svg width="142" height="80" viewBox="0 0 142 80">
      <path d="M142 0H100C78 8 70 30 80 54C88 70 104 78 118 80H142Z" fill="#a9aaac"/>
      <path d="M142 0H104C84 10 78 32 88 52C96 66 110 74 126 76C132 77 138 78 142 80Z" fill="#f4f4f4"/>
    </svg>
    <div class="card-front-details">
      <div class="card-name">DALE CORRIN</div>
      <div class="tiny">CEO<br>Agile Coach &amp; Trainer</div>
      <div class="tiny" style="margin-top:3px">PO Box 4417<br>Kelbrook Lower<br>VIC 3190, Australia</div>
      <div class="tiny" style="margin-top:3px">+61 400 555 217<br>dale@moxyfen.com.au<br>www.moxyfen.com.au</div>
    </div>
    <div class="wordmark">Moxy Fen</div>
  </section>

  <section class="sheet card-back" aria-label="Business card back">
    <svg width="142" height="80" viewBox="0 0 142 80">
      <path d="M104 0H142V80H100C116 62 118 22 104 0Z" fill="#3d65a3"/>
    </svg>
    <div class="card-back-text">
      <div class="wordmark">Moxy Fen</div>
      <div class="card-back-phone">1300MOXYFEN</div>
    </div>
  </section>

  <section class="sheet envelope-front" aria-label="Envelope front">
    <div class="wordmark"><span class="wordmark-dot"></span>Moxy Fen</div>
    <div class="tiny">PO Box 4417<br>Kelbrook Lower<br>VIC 3190, Australia</div>
  </section>

  <section class="sheet envelope-back" aria-label="Envelope back">
    <svg width="351" height="60" viewBox="0 0 351 60">
      <path d="M0 0H351V4L342 32Q340 38 334 38L196 58Q175 61 154 58L17 38Q11 38 9 32L0 4Z" fill="#3d65a3"/>
    </svg>
    <div class="envelope-flap-mark">
      <div class="wordmark">Moxy Fen</div>
      <div class="tiny">www.moxyfen.com.au</div>
    </div>
  </section>

  <section class="sheet compliments" aria-label="Compliments slip">
    <div class="wordmark"><span class="wordmark-dot"></span>Moxy Fen</div>
    <div class="compliments-script">With Compliments</div>
    <div class="compliments-footer">
      <div class="tiny">PO Box 4417, Kelbrook Lower, VIC 3190, Australia</div>
      <div class="tiny">P: 1300MOXYFEN&nbsp; M: +61 400 555 217&nbsp; E: dale@moxyfen.com.au</div>
      <div class="compliments-rule"></div>
      <div class="tiny compliments-web">www.moxyfen.com.au</div>
    </div>
  </section>

</body>
</html>
```